RW Holloway LLC Business Card - Civil Engineering & Consulting Firm

We need a Business Card that is elegant, and masculine.  It is our Professional Civil Engineering & Consulting Company located in San Antonio TX (Not s construction or builder firm- no gears & no tool images please). We provide civil engineering services including  commercial site plans, grading and drainage plans, utility plans, hydraulics and hydrology, land planning, utility coordination, and other general civil engineering services related to commercial and residential development.
We have 2 existing Logos. We would like to convey reliability, strength, trustworthiness and attention to detail.  Blues and orange tones as per logo We are OK with the use of a darker blue in the mix.  We have 2 logo versions - Full Company Name Logo to go on the back of card, & Small Icon Logo for the front w/ personal Info.

Target Market(s)
Architects, Real Estate Developers, Other Strctural Engineers, Surveyers, General Contractors
Industry/Entity Type
Professional Civil Engineering
Contact Information for Business Card
Name, Position, Address, Cell & Office #, email, and company website
Font styles to use
Other font styles liked:
- Avian
Requirements
Should not have
- No Tools, No Gears, no Cranes, or Construction Equipment.

```html
<!DOCTYPE html>
<html lang="en">
<head>
<meta charset="utf-8">
<title>RW Holloway LLC — Business Card</title>
<link href="https://fonts.googleapis.com/css2?family=Montserrat:wght@400;500;700&display=swap" rel="stylesheet">
<style>
  :root {
    --stage: #3b3b3b;
    --card: #1a1a1b;
    --card-edge: #7fa8d8;
    --blue: #6e9fd6;
    --orange: #f0962a;
    --white: #ededed;
    --pattern-a: #121213;
    --pattern-b: #2e2e31;
  }
  * { margin: 0; padding: 0; box-sizing: border-box; }
  html, body { width: 1200px; height: 801px; overflow: hidden; }
  body {
    background: var(--stage);
    font-family: "Montserrat", sans-serif;
    display: flex;
    align-items: center;
    justify-content: center;
    gap: 40px;
  }
  .card {
    position: relative;
    width: 540px;
    height: 309px;
    background: var(--card);
    border-bottom: 3px solid var(--card-edge);
    overflow: hidden;
  }
  /* Front */
  .brand {
    position: absolute;
    left: 36px;
    top: 100px;
  }
  .brand-name {
    color: var(--blue);
    font-size: 30px;
    font-weight: 400;
    letter-spacing: 3px;
    line-height: 1;
  }
  .brand-tag {
    color: var(--orange);
    font-size: 8px;
    letter-spacing: 3px;
    margin-top: 9px;
  }
  .person {
    position: absolute;
    right: 36px;
    top: 40px;
    text-align: right;
  }
  .person-name {
    color: var(--blue);
    font-size: 18px;
    font-weight: 700;
    letter-spacing: 0.5px;
  }
  .person-role {
    color: var(--white);
    font-size: 12px;
    margin-top: 3px;
  }
  .divider {
    position: absolute;
    left: 36px;
    right: 36px;
    top: 176px;
    height: 1px;
    background: var(--blue);
  }
  .contacts {
    position: absolute;
    left: 36px;
    top: 192px;
    list-style: none;
    color: var(--white);
    font-size: 12px;
    line-height: 1.6;
  }
  .contacts li { display: flex; align-items: center; gap: 8px; }
  .contacts svg { width: 10px; height: 10px; flex: none; }
  .address {
    position: absolute;
    right: 36px;
    top: 192px;
    text-align: right;
    color: var(--white);
    font-size: 12px;
    line-height: 1.6;
  }
  /* Back */
  .pattern-field {
    position: absolute;
    inset: 0;
    background:
      radial-gradient(ellipse at 75% 30%, rgba(70,70,76,0.55) 0%, transparent 60%),
      linear-gradient(135deg, var(--pattern-a) 0%, var(--pattern-b) 55%, var(--pattern-a) 100%);
  }
  .back-mark {
    position: absolute;
    right: 110px;
    top: 50%;
    transform: translateY(-50%);
    color: var(--orange);
    font-size: 13px;
    font-weight: 500;
    letter-spacing: 2px;
  }
</style>
</head>
<body>
  <section class="card card-front">
    <div class="person">
      <div class="person-name">DANIEL WHITCOMB</div>
      <div class="person-role">President</div>
    </div>
    <div class="brand">
      <div class="brand-name">RW HOLLOWAY</div>
      <div class="brand-tag">LLC · CONSULTING ENGINEERS</div>
    </div>
    <div class="divider"></div>
    <ul class="contacts">
      <li><svg viewBox="0 0 10 10"><rect x="2" y="0.5" width="6" height="9" rx="1" fill="none" stroke="#f0962a" stroke-width="1.2"/></svg>555-310-4827</li>
      <li><svg viewBox="0 0 10 10"><path d="M2 1 L4 1 L5 3.5 L3.8 4.5 Q5 6.5 5.8 6.4 L7 5 L9 6 L9 8 Q6 10 3 7 Q0 4 2 1Z" fill="#f0962a"/></svg>555-310-4827</li>
      <li><svg viewBox="0 0 10 10"><rect x="0.5" y="2" width="9" height="6" fill="#f0962a"/><path d="M0.5 2 L5 5.5 L9.5 2" fill="none" stroke="#1a1a1b" stroke-width="1"/></svg>info@rwhollowayconsulting.com</li>
      <li><svg viewBox="0 0 10 10"><circle cx="5" cy="5" r="4.5" fill="#f0962a"/><path d="M0.5 5 H9.5 M5 0.5 V9.5" stroke="#1a1a1b" stroke-width="0.8"/></svg>www.rwhollowayconsulting.com</li>
    </ul>
    <div class="address">1480 Harbor Crest Drive<br>Seacliff CA 90412</div>
  </section>

  <section class="card card-back">
    <div class="pattern-field" role="img" aria-label="Tone-on-tone repeating monogram pattern in dark gloss covering the card back"></div>
    <div class="back-mark">RW HOLLOWAY</div>
  </section>
</body>
</html>
```